Copper Ridge Inquiries Letterhead

I would like to design a letterhead for a private investigation company. Our primary clients will be law firms. The business card is included below

```html
<!DOCTYPE html>
<html lang="en">
<head>
<meta charset="utf-8">
<title>Copper Ridge Inquiries Letterhead</title>
<link href="https://fonts.googleapis.com/css2?family=Lato:wght@400;700&family=Montserrat:wght@400;800&display=swap" rel="stylesheet">
<style>
  :root {
    --navy: #1b355f;
    --orange: #f15a2b;
    --ink: #1a1a1a;
    --paper: #ffffff;
    --backdrop: #e2e2e2;
  }
  * { margin: 0; padding: 0; box-sizing: border-box; }
  html, body { width: 1200px; height: 1141px; overflow: hidden; }
  body { background: var(--backdrop); font-family: "Lato", Arial, sans-serif; color: var(--ink); }
  .letterhead {
    position: absolute; left: 210px; top: 20px;
    width: 779px; height: 1101px;
    background: var(--paper);
    box-shadow: 0 2px 10px rgba(0,0,0,0.15);
    overflow: hidden;
  }
  .header-band {
    position: absolute; left: 0; top: 0; width: 779px; height: 126px;
    background: var(--navy);
  }
  .header-rule {
    position: absolute; left: 0; top: 130px; width: 779px; height: 4px;
    background: var(--orange);
  }
  .contact {
    position: absolute; left: 386px; top: 31px;
    font-family: "Montserrat", Arial, sans-serif; font-size: 13.5px;
    color: #fff; letter-spacing: 0.1px; line-height: 19.5px;
  }
  .contact-row { display: flex; align-items: center; gap: 7px; }
  .contact-row svg { width: 12px; height: 12px; flex: none; }
  .license { margin-top: 8px; }
  .brand { position: absolute; left: 38px; top: 152px; width: 182px; text-align: center; }
  .brand-dot { width: 80px; height: 80px; border-radius: 50%; background: var(--orange); margin: 0 auto 18px; }
  .brand-name {
    font-family: "Montserrat", Arial, sans-serif; font-weight: 800;
    font-size: 22px; line-height: 25px; color: var(--navy);
  }
  .letter { position: absolute; left: 39px; width: 702px; font-size: 15.6px; line-height: 17.3px; }
  .date { top: 347px; font-size: 16px; }
  .recipient { top: 385px; font-size: 15.5px; line-height: 18.5px; }
  .company { top: 439px; font-size: 15.5px; line-height: 18.5px; }
  .salutation { top: 518px; font-size: 20px; font-weight: 700; }
  .body { top: 557px; }
  .body p { text-align: justify; margin-bottom: 17px; }
  .closing { top: 875px; font-size: 15.5px; }
  .signature {
    position: absolute; left: 39px; top: 950px; width: 214px; height: 32px;
    background: linear-gradient(90deg, #d6d6d6, #ececec);
  }
</style>
</head>
<body>
  <main class="letterhead">
    <div class="header-band"></div>
    <div class="header-rule"></div>

    <div class="contact">
      <div class="contact-row">
        <svg viewBox="0 0 12 12"><path fill="var(--orange)" d="M6 0.5a4 4 0 0 0-4 4c0 3 4 7 4 7s4-4 4-7a4 4 0 0 0-4-4zm0 5.6a1.6 1.6 0 1 1 0-3.2 1.6 1.6 0 0 1 0 3.2z"/></svg>
        <span>BROOKHAVEN, OR</span>
      </div>
      <div class="contact-row">
        <svg viewBox="0 0 12 12"><path fill="var(--orange)" d="M1 4.5C1 3 3 2 6 2s5 1 5 2.5v1H8.5V4.3h-5v1.2H1zM3 6h6l1.5 4h-9z"/></svg>
        <span>541.555.0192</span>
      </div>
      <div class="contact-row">
        <svg viewBox="0 0 12 12"><rect x="1" y="2.5" width="10" height="7" rx="1" fill="var(--orange)"/><path d="M1.5 3l4.5 3.5L10.5 3" stroke="#fff" stroke-width="1" fill="none"/></svg>
        <span>DANA@COPPERRIDGEINQUIRIES.COM</span>
      </div>
      <div class="license">LICENSE NO. 04417352</div>
    </div>

    <div class="brand">
      <div class="brand-dot"></div>
      <div class="brand-name">COPPER RIDGE<br>INQUIRIES</div>
    </div>

    <div class="letter date">January-03-2020</div>
    <div class="letter recipient">Mr, John Doe<br>President</div>
    <div class="letter company">Link Corpporation<br>123 Street Name, Suite# 10<br>City, State, 120023</div>
    <div class="letter salutation">Dear Mr, John</div>
    <div class="letter body">
      <p>Lorem ipsum dolor sit amet, consectetur adipiscing elit, sed do eiusmod tempor incididunt ut labore et dolore magna aliqua. Ut enim ad minim veniam, quis nostrud exercitation ullamco laboris nisi ut aliquip ex ea commodo consequat. Duis aute irure dolor in reprehenderit in voluptate velit esse cillum dolore eu fugiat nulla pariatur.</p>
      <p>Lorem ipsum dolor sit amet, consectetur adipiscing elit, sed do eiusmod tempor incididunt ut labore et dolore magna aliqua. Ut enim ad minim veniam, quis nostrud exercitation ullamco laboris nisi ut aliquip ex ea commodo consequat. Duis aute irure dolor in reprehenderit in voluptate velit esse cillum dolore eu fugiat nulla pariatur.</p>
      <p>Lorem ipsum dolor sit amet, consectetur adipiscing elit, sed do eiusmod tempor incididunt ut labore et dolore magna aliqua. Ut enim ad minim veniam, quis nostrud exercitation ullamco laboris nisi ut aliquip ex ea commodo consequat.</p>
      <p>Excepteur sint occaecat cupidatat non proident, sunt in culpa qui officia deserunt mollit anim id est laborum. re et dolore magnam aliquam quaerat voluptatem.</p>
    </div>
    <div class="letter closing">Regards</div>
    <div class="signature" role="img" aria-label="Handwritten signature of Dana Whitford"></div>
  </main>
</body>
</html>
```